Calm Summit website development

Need a website designed for a coaching business. Very high-end, luxury, professionalism, in the area of STRESS, see brief attached. I have a logo already
Updates

Slow in providing feedback

Target Market(s)

CEOs very successful men and wealthy females, high end luxury market

Industry/Entity Type

coaching

Number of Pages Required

1 page

Requirements
Must have
• Luxury look, professional, serious but warm, appealing to both sexes

```html
<!DOCTYPE html>
<html lang="en">
<head>
<meta charset="utf-8">
<title>Calm Summit – Lifestyle Coaching</title>
<link href="https://fonts.googleapis.com/css2?family=Oswald:wght@500;600&family=Montserrat:wght@500;600;700;800&family=Lato:wght@400;700&display=swap" rel="stylesheet">
<style>
:root{
  --blue:#0a7fd0;
  --ink:#1d1d1f;
  --text:#333;
  --soft:#f4f2f3;
  --hex:#5a5a5c;
  --footer:#2b2a2b;
  --white:#fff;
}
*{margin:0;padding:0;box-sizing:border-box}
html,body{width:1200px;height:3458px;overflow:hidden}
body{position:relative;background:var(--white);font-family:'Lato',sans-serif;color:var(--text)}
.btn{position:absolute;display:flex;align-items:center;justify-content:center;gap:10px;background:var(--blue);color:var(--white);font-family:'Montserrat',sans-serif;font-weight:500;font-size:13px;text-decoration:none}
.btn svg{width:26px;height:8px}

/* hero */
.hero{position:absolute;left:0;top:0;width:1200px;height:652px;background:linear-gradient(90deg,#fffdf7 0%,#fffdf7 100%)}
.hero-sky{position:absolute;left:0;top:0;width:700px;height:652px;
  background:linear-gradient(180deg,#f3efe6 0%,#ece6da 35%,#b9bab6 50%,#9fa39f 60%,#c9b07a 72%,#b89445 86%,#8d6d2c 100%)}
.hero-figure{position:absolute;left:150px;top:160px;width:400px;height:492px;
  background:linear-gradient(180deg,#e8c9a8 0%,#efe7da 30%,#f4efe6 60%,#d9cdb6 100%);border-radius:180px 180px 0 0}
.hero-fade{position:absolute;left:560px;top:0;width:260px;height:652px;background:linear-gradient(90deg,rgba(255,253,247,0) 0%,#fffdf7 100%)}
.hero-field{position:absolute;left:0;top:520px;width:1200px;height:132px;background:linear-gradient(180deg,rgba(201,170,100,0) 0%,#c9a45a 55%,#a7843b 100%)}
.brand{position:absolute;left:132px;top:22px;width:132px;text-align:center}
.brand-mark{width:38px;height:38px;background:var(--ink);margin:0 auto 14px}
.brand-name{font-family:'Oswald',sans-serif;font-weight:600;font-size:18px;letter-spacing:3px;color:var(--ink);white-space:nowrap}
.nav{position:absolute;left:456px;top:47px;display:flex;font-family:'Montserrat',sans-serif;font-size:13px;font-weight:500;color:var(--ink)}
.nav a{color:inherit;text-decoration:none;margin-right:38px;letter-spacing:.3px}
.nav a.active{color:var(--blue);font-weight:700;border-bottom:2px solid var(--blue);padding-bottom:6px}
.consult{position:absolute;left:1074px;top:0;width:126px;height:99px;background:var(--blue);color:var(--white);font-family:'Montserrat',sans-serif;font-size:15px;line-height:21px;padding:19px 0 0 24px}
.consult svg{width:32px;height:8px;vertical-align:middle;margin-left:8px}
.hero-title{position:absolute;left:710px;top:216px;font-family:'Oswald',sans-serif;font-weight:600;font-size:62px;letter-spacing:9px;color:var(--ink);line-height:1}
.hero-text{position:absolute;left:710px;top:303px;width:370px;font-size:16.5px;line-height:25px;color:#222}
.dots{position:absolute;left:571px;top:613px;display:flex;gap:6px}
.dots span{width:8px;height:8px;border-radius:50%;background:rgba(255,255,255,.9)}
.dots span.on{background:var(--blue)}

/* audiences */
.soft{position:absolute;left:0;top:652px;width:1200px;height:827px;background:var(--soft)}
.hex-card{position:absolute;top:691px;width:268px;height:322px;clip-path:polygon(50% 0,100% 25%,100% 75%,50% 100%,0 75%,0 25%)}
.hex-card .label{position:absolute;left:0;top:235px;width:100%;height:36px;background:rgba(255,255,255,.88);display:flex;align-items:center;justify-content:center;gap:14px;font-family:'Montserrat',sans-serif;font-weight:600;font-size:14px;color:var(--ink);letter-spacing:.5px}
.hex-card .label svg{width:26px;height:8px}
.hex-card .base{position:absolute;left:0;top:271px;width:100%;height:51px}
.men{left:156px;background:linear-gradient(160deg,#f1f2f3 0%,#d6d9dd 35%,#8e97a5 55%,#2c3447 75%,#1c2233 100%)}
.men .base{background:#4a4c52}
.women{left:468px;background:linear-gradient(180deg,#fbe3b8 0%,#f3b96b 40%,#d98d43 62%,#7e5637 80%,#3f2a1f 100%)}
.women .base{background:linear-gradient(180deg,#8a5a2e,#5a3a22)}
.athletes{left:778px;background:linear-gradient(180deg,#7d98b9 0%,#c9c9c0 30%,#f4dca8 48%,#e2a85e 62%,#7a5a3e 78%,#2a2a2e 100%)}
.athletes .base{background:#2a2a2e}

.welcome-photo{position:absolute;left:94px;top:1037px;width:436px;height:442px;
  background:linear-gradient(180deg,#e9e6e5 0%,#d8d3d1 30%,#bdb6b3 55%,#8e8886 78%,#a24a38 100%);
  clip-path:polygon(40% 0,100% 0,100% 100%,30% 100%,0 35%)}
.kicker{position:absolute;left:581px;top:1104px;font-family:'Montserrat',sans-serif;font-weight:500;font-size:17px;color:var(--ink)}
.welcome-title{position:absolute;left:581px;top:1128px;font-family:'Montserrat',sans-serif;font-weight:500;font-size:33px;color:var(--ink);letter-spacing:.5px}
.rule{position:absolute;height:1px;background:var(--ink)}
.welcome-text{position:absolute;left:581px;top:1209px;width:488px;font-size:13.6px;line-height:20.8px;color:#333}

/* benefits */
.benefits{position:absolute;left:130px;top:1541px;width:757px;height:547px;border:1.5px solid #666}
.benefits h2{position:absolute;left:32px;top:26px;font-family:'Montserrat',sans-serif;font-weight:700;font-size:27px;color:var(--ink);letter-spacing:.5px}
.benefit{position:absolute;left:32px;display:flex;align-items:center;width:500px}
.benefit svg{flex:0 0 54px;width:54px;height:60px;margin-right:20px}
.benefit p{font-size:13.6px;line-height:20.5px;color:#333;width:410px}
.photo{position:absolute}
.ph-desk{left:718px;top:1594px;width:341px;height:253px;background:linear-gradient(120deg,#e4e9ec 0%,#b9c8d2 35%,#5d87ad 60%,#2f5f8f 80%,#8c9aa5 100%)}
.ph-gym{left:718px;top:1856px;width:133px;height:173px;background:linear-gradient(180deg,#d5d3cf 0%,#9b928a 40%,#3a3836 75%,#2a2826 100%)}
.ph-yoga{left:862px;top:1856px;width:197px;height:173px;background:linear-gradient(180deg,#a99fa6 0%,#e0bfa6 40%,#f6c993 55%,#6d6266 75%,#3e3a3d 100%)}

/* banner */
.banner{position:absolute;left:130px;top:2135px;width:940px;height:428px;background:linear-gradient(100deg,#5b7690 0%,#2f4d70 30%,#3e5878 50%,#6f7480 70%,#a28665 88%,#b08a5e 100%)}
.banner h2{position:absolute;left:532px;top:66px;font-family:'Montserrat',sans-serif;font-weight:800;font-size:27px;line-height:33px;color:var(--white);letter-spacing:.3px}
.banner p{position:absolute;left:532px;top:148px;width:380px;font-size:16.5px;line-height:21px;color:var(--white)}

/* why me */
.why{position:absolute;left:0;top:2597px;width:1200px;height:530px;background:linear-gradient(90deg,#fffefb 0%,#fbf6e8 45%,#f3e2b8 72%,#d9c49a 100%)}
.why-figure{position:absolute;left:820px;top:30px;width:360px;height:420px;border-radius:160px 160px 20px 20px;
  background:linear-gradient(180deg,#6e5d52 0%,#c7ad92 30%,#b39a80 55%,#5f5346 100%)}
.why-grass{position:absolute;left:0;top:400px;width:1200px;height:130px;background:linear-gradient(180deg,rgba(150,160,90,0) 0%,#8a9a50 55%,#4d6a2c 100%)}
.why h2{position:absolute;left:132px;top:131px;font-family:'Montserrat',sans-serif;font-weight:700;font-size:25px;color:var(--ink);letter-spacing:.5px}
.why p{position:absolute;left:132px;width:470px;font-size:13.6px;line-height:20.8px;color:#333}

/* footer */
.footer{position:absolute;left:0;top:3127px;width:1200px;height:331px;background:var(--footer);color:var(--white);font-family:'Montserrat',sans-serif}
.footer .brand{left:158px;top:50px;width:202px}
.footer .brand-mark{width:64px;height:64px;background:var(--white);margin-bottom:22px}
.footer .brand-name{color:var(--white);font-size:25px;letter-spacing:5px}
.f-head{position:absolute;top:44px;font-weight:700;font-size:12.5px;letter-spacing:.3px}
.f-menu{position:absolute;left:458px;top:82px;list-style:none;font-size:11px;line-height:19.6px}
.f-item{position:absolute;display:flex;align-items:center;font-size:11px;line-height:15px}
.f-item .dot{width:22px;height:22px;border-radius:50%;background:var(--white);margin-right:11px;display:flex;align-items:center;justify-content:center}
.f-item .dot svg{width:11px;height:11px}
.f-rule{position:absolute;left:134px;top:3383px;width:933px;height:1px;background:#4a494b}
.copy{position:absolute;left:0;top:3417px;width:1200px;text-align:center;font-family:'Montserrat',sans-serif;font-size:10.5px;color:var(--white)}
</style>
</head>
<body>

<section class="hero">
  <div class="hero-sky" role="img" aria-label="Photo of hazy mountains above a golden meadow"></div>
  <div class="hero-figure" role="img" aria-label="Photo of a smiling woman in a white dress with arms spread wide"></div>
  <div class="hero-fade"></div>
  <div class="hero-field" role="img" aria-label="Sunlit golden grass"></div>
</section>

<div class="brand">
  <div class="brand-mark"></div>
  <div class="brand-name">CALM SUMMIT</div>
</div>

<nav class="nav">
  <a class="active" href="#">HOME</a>
  <a href="#">ABOUT US</a>
  <a href="#">TRAINING</a>
  <a href="#" style="margin-right:42px">SUCCESS TORIES</a>
  <a href="#" style="margin-right:32px">BLOG</a>
  <a href="#">CONTACT</a>
</nav>

<div class="consult">Schedule<br>Free<svg viewBox="0 0 32 8"><path d="M0 4H30M26 1L30 4 26 7" stroke="#fff" stroke-width="1.2" fill="none"/></svg><br>Consult</div>

<h1 class="hero-title">HEAD COACH</h1>
<p class="hero-text">Not your typical “quiet whale music playing in the background, kind of “stress guy”….stress is good, it can save your life…</p>
<a class="btn" href="#" style="left:714px;top:401px;width:126px;height:43px">Read More <svg viewBox="0 0 26 8"><path d="M0 4H24M20 1L24 4 20 7" stroke="#fff" stroke-width="1.2" fill="none"/></svg></a>
<div class="dots"><span></span><span></span><span class="on"></span><span></span><span></span></div>

<section class="soft"></section>

<div class="hex-card men" role="img" aria-label="Photo of a cheering businessman in a suit">
  <div class="label">MEN <svg viewBox="0 0 26 8"><path d="M0 4H24M20 1L24 4 20 7" stroke="#1d1d1f" stroke-width="1.2" fill="none"/></svg></div>
  <div class="base"></div>
</div>
<div class="hex-card women" role="img" aria-label="Photo of a woman leaping at sunset over hills">
  <div class="label">WOMEN <svg viewBox="0 0 26 8"><path d="M0 4H24M20 1L24 4 20 7" stroke="#1d1d1f" stroke-width="1.2" fill="none"/></svg></div>
  <div class="base"></div>
</div>
<div class="hex-card athletes" role="img" aria-label="Photo of two runners sprinting into the sun">
  <div class="label">ATHLETES <svg viewBox="0 0 26 8"><path d="M0 4H24M20 1L24 4 20 7" stroke="#1d1d1f" stroke-width="1.2" fill="none"/></svg></div>
  <div class="base"></div>
</div>

<div class="welcome-photo" role="img" aria-label="Photo of a joyful woman in a striped top raising her arms"></div>
<p class="kicker">WELCOME TO</p>
<h2 class="welcome-title">CALMSUMMIT</h2>
<div class="rule" style="left:581px;top:1181px;width:245px"></div>
<p class="welcome-text">Calm Summit came about due to my desire to help people lead a better and healthier life. Initially, I was involved in the fitness/body side of health. As years passed and my experience grew, I realized how important the mind was in total wellness, and that the mind is all powerful and controlling. Control the mind, control the body and achieve success. Stress can be the most debilating factor in our lives, it is the root cause of so many diseases and costs the US workplace an estimated 300 billion dollars due to loss of productivity.</p>
<a class="btn" href="#" style="left:586px;top:1384px;width:127px;height:44px">Read More <svg viewBox="0 0 26 8"><path d="M0 4H24M20 1L24 4 20 7" stroke="#fff" stroke-width="1.2" fill="none"/></svg></a>

<section class="benefits">
  <h2>BENEFITS</h2>
  <div class="rule" style="left:32px;top:66px;width:49px"></div>
  <div class="benefit" style="top:100px">
    <svg viewBox="0 0 54 60"><path d="M27 0L54 15V45L27 60 0 45V15Z" fill="#5a5a5c"/></svg>
    <p>Experience</p>
  </div>
  <div class="benefit" style="top:178px">
    <svg viewBox="0 0 54 60"><path d="M27 0L54 15V45L27 60 0 45V15Z" fill="#5a5a5c"/><circle cx="27" cy="22" r="4" fill="#fff"/><path d="M27 28V44M18 26C22 36 27 36 27 36M36 26C32 36 27 36 27 36" stroke="#fff" stroke-width="2.5" fill="none"/></svg>
    <p>Sector expert Health/Wellness. Presented at numerous industry shows and quoted in national publications (not as a coach, I’m new, but in the health &amp; wellness space)</p>
  </div>
  <div class="benefit" style="top:260px">
    <svg viewBox="0 0 54 60"><path d="M27 0L54 15V45L27 60 0 45V15Z" fill="#5a5a5c"/><path d="M21 26C21 18 34 18 34 26C34 32 28 33 28 38C28 42 22 42 22 39" stroke="#fff" stroke-width="3" fill="none"/></svg>
    <p>Excellent listener…being in sales for many years, the secret is to really listen…and get to the end game, and make it feel as if it was their decision. Not sure how to word this as a benefit.</p>
  </div>
  <div class="benefit" style="top:350px">
    <svg viewBox="0 0 54 60"><path d="M27 0L54 15V45L27 60 0 45V15Z" fill="#5a5a5c"/><circle cx="18" cy="22" r="3.5" fill="#fff"/><circle cx="36" cy="22" r="3.5" fill="#fff"/><path d="M14 28V40H22M40 28V40H32M22 34H32" stroke="#fff" stroke-width="3" fill="none"/></svg>
    <p>Access/resources industry professionals, sport psychologist…just spent a few hours with the Mind performance coach for the Harbor City Comets baseball team…I can get the best advice and latest techniques in mind/body training performance.</p>
  </div>
  <div class="benefit" style="top:445px">
    <svg viewBox="0 0 54 60"><path d="M27 0L54 15V45L27 60 0 45V15Z" fill="#5a5a5c"/><rect x="18" y="18" width="16" height="22" fill="#fff"/><path d="M21 24H31M21 29H31M21 34H27" stroke="#5a5a5c" stroke-width="1.5"/></svg>
    <p>Private, more than happy to sign confidentiality agreement. Especially for the business man.</p>
  </div>
</section>
<div class="photo ph-desk" role="img" aria-label="Photo of a man relaxing at his desk by a city window"></div>
<div class="photo ph-gym" role="img" aria-label="Photo of a man stretching in a gym"></div>
<div class="photo ph-yoga" role="img" aria-label="Photo of a woman meditating in a yoga pose at sunset"></div>

<section class="banner" role="img" aria-label="Photo of a confident man in a blazer sitting on stadium steps">
  <h2>HOW TO LIVE AND WORK<br>FROM THE UNSEEN REALM</h2>
  <p>There are many variations of passages of Lorem Ipsum available, but the majority have suffered alteration in some form, by injected humour, or randomised words which don’t look even slightly believable.</p>
  <a class="btn" href="#" style="left:534px;top:277px;width:126px;height:44px">Read More <svg viewBox="0 0 26 8"><path d="M0 4H24M20 1L24 4 20 7" stroke="#fff" stroke-width="1.2" fill="none"/></svg></a>
</section>

<section class="why">
  <div class="why-figure" role="img" aria-label="Photo of a woman in a knit hat sipping coffee in a sunny field"></div>
  <div class="why-grass" role="img" aria-label="Sunlit green grass"></div>
  <h2>WHY ME?</h2>
  <div class="rule" style="left:132px;top:170px;width:48px"></div>
  <p style="top:218px">Been there done that! Have been through a lot, started businesses, selling a business, law suits, marriage, divorce, second marriage, kids, school, sports, fights, robbed, gun in face, traveled the world, successful, two great kids (both Cadets at Ridgeview Academy…duty/honor/country)</p>
  <p style="top:332px;width:450px">Limited number of clients…different stage of life, empty nester, have a full career…won’t be a number</p>
</section>

<footer class="footer">
  <div class="brand">
    <div class="brand-mark"></div>
    <div class="brand-name">CALM SUMMIT</div>
  </div>

  <h3 class="f-head" style="left:458px">MENU</h3>
  <ul class="f-menu">
    <li>HOME</li><li>ABOUT US</li><li>TRAINING</li><li>SUCCESS STORIES</li><li>BLOG</li><li>CONTACT</li>
  </ul>

  <h3 class="f-head" style="left:655px">CONTACT US</h3>
  <div class="f-item" style="left:653px;top:82px">
    <span class="dot"><svg viewBox="0 0 12 12"><path d="M6 1C3.8 1 2.5 2.6 2.5 4.5 2.5 7 6 11 6 11S9.5 7 9.5 4.5C9.5 2.6 8.2 1 6 1Z" fill="#2b2a2b"/><circle cx="6" cy="4.6" r="1.3" fill="#fff"/></svg></span>
    <span>4120 Lakeshore Ave Suite 200<br>Fairview, FL 32000</span>
  </div>
  <div class="f-item" style="left:653px;top:134px">
    <span class="dot"><svg viewBox="0 0 12 12"><path d="M3 1.5L5 3.5 4 5C4.7 6.6 5.6 7.6 7 8.2L8.5 7 10.5 9 9.2 10.5C5.5 10.5 1.5 6.5 1.5 2.8Z" fill="#2b2a2b"/></svg></span>
    <span>Call Us<br>555.010.0199</span>
  </div>
  <div class="f-item" style="left:653px;top:186px">
    <span class="dot"><svg viewBox="0 0 12 12"><rect x="1.5" y="3" width="9" height="6.5" fill="#2b2a2b"/><path d="M1.5 3L6 6.5 10.5 3" stroke="#fff" stroke-width="1" fill="none"/></svg></span>
    <span>E mail Us<br>hello@calmsummit.com</span>
  </div>

  <h3 class="f-head" style="left:966px">FOLLOW US</h3>
  <div class="f-item" style="left:966px;top:84px"><span class="dot"></span><span>Like us on<br>FRIENDLOOP</span></div>
  <div class="f-item" style="left:966px;top:134px"><span class="dot"></span><span>Follow us on<br>CHIRPLINE</span></div>
  <div class="f-item" style="left:966px;top:185px"><span class="dot"></span><span>Follow us on<br>WORKGRAPH</span></div>
</footer>
<div class="f-rule"></div>
<p class="copy">Copyright © 2022 All Rights Reserved</p>

</body>
</html>
```